New LLC consulting company needs a business card design

I need a business card design for new company in Alexandria Virginia called TK Verdane Consulting LLC. The company is focused on consulting for defense and national security issues with expertise in nuclear and space topics. I would like to see designs that are simple and I am open to colors except for brown.

Target Market(s)

All businesses that are seeking consulting help

Industry/Entity Type

Consulting

Contact Information for Business Card

Name of company - TK Verdane Consulting LLC; name (Delia Pratt) President; email: prattdq47@mailvessa.com; Phone: 703-555-0142

Requirements
Must have
• The details described above
Nice to have
• I'm open to all ideas
Should not have
• No brown

```html
<!DOCTYPE html>
<html lang="en">
<head>
<meta charset="utf-8">
<title>TK Verdane Consulting LLC — Business Card</title>
<link href="https://fonts.googleapis.com/css2?family=Lato:wght@400;700;900&display=swap" rel="stylesheet">
<style>
  :root {
    --navy: #1a3045;
    --sky: #6ab8dc;
    --paper: #ffffff;
    --backdrop: #2f2f2f;
    --ink-soft: #2b3d50;
  }
  * { box-sizing: border-box; margin: 0; padding: 0; }
  html, body {
    width: 1200px; height: 875px; overflow: hidden;
    background: var(--backdrop);
    font-family: "Lato", Arial, sans-serif;
  }
  .canvas {
    width: 1200px; height: 875px;
    display: flex; flex-direction: column;
    align-items: center; justify-content: center; gap: 56px;
  }
  .card {
    position: relative;
    width: 560px; height: 320px;
    border-radius: 16px;
    overflow: hidden;
  }
  .card--front { background: var(--navy); }
  .card--back { background: var(--paper); }

  .wordmark {
    position: absolute;
    display: flex; align-items: center; gap: 18px;
  }
  .wordmark__dot {
    border-radius: 50%;
    background: var(--sky);
    flex: none;
  }
  .wordmark__name {
    font-weight: 700;
    text-transform: uppercase;
    line-height: 1.05;
    letter-spacing: 0.04em;
  }
  .card--front .wordmark { left: 50%; top: 50%; transform: translate(-50%, -50%); }
  .card--front .wordmark__dot { width: 78px; height: 78px; }
  .card--front .wordmark__name { color: var(--paper); font-size: 34px; }
  .card--front .wordmark__name span { display: block; font-size: 17px; letter-spacing: 0.16em; margin-top: 6px; }

  .card--back .wordmark { left: 40px; top: 120px; gap: 12px; }
  .card--back .wordmark__dot { width: 46px; height: 46px; }
  .card--back .wordmark__name { color: var(--navy); font-size: 21px; }
  .card--back .wordmark__name span { display: block; font-size: 10px; letter-spacing: 0.16em; margin-top: 4px; }

  .contact {
    position: absolute; left: 292px; top: 92px;
    color: var(--navy);
  }
  .contact__name {
    font-weight: 900; font-size: 24px; letter-spacing: 0.03em;
    text-transform: uppercase;
  }
  .contact__role {
    color: var(--sky); font-size: 14px; margin-top: 2px;
  }
  .contact__rule {
    width: 48px; height: 1.5px; background: var(--navy);
    margin: 8px 0 10px;
  }
  .contact__line {
    display: flex; align-items: center; gap: 8px;
    font-size: 13px; color: var(--ink-soft); margin-top: 5px;
  }
  .contact__line svg { width: 12px; height: 12px; flex: none; }

  .card__band {
    position: absolute; left: 0; bottom: 0;
    width: 560px; height: 26px;
  }
</style>
</head>
<body>
  <main class="canvas">
    <section class="card card--front" aria-label="Card front">
      <div class="wordmark">
        <div class="wordmark__dot"></div>
        <div class="wordmark__name">TK Verdane<span>Consulting LLC</span></div>
      </div>
    </section>

    <section class="card card--back" aria-label="Card back">
      <div class="wordmark">
        <div class="wordmark__dot"></div>
        <div class="wordmark__name">TK Verdane<span>Consulting LLC</span></div>
      </div>

      <div class="contact">
        <div class="contact__name">Delia Pratt</div>
        <div class="contact__role">President</div>
        <div class="contact__rule"></div>
        <div class="contact__line">
          <svg viewBox="0 0 24 24" aria-hidden="true"><path fill="var(--sky)" d="M6.6 10.8a15.1 15.1 0 0 0 6.6 6.6l2.2-2.2c.3-.3.7-.4 1-.2 1.1.4 2.3.6 3.6.6.6 0 1 .4 1 1V20c0 .6-.4 1-1 1A17 17 0 0 1 3 4c0-.6.4-1 1-1h3.5c.6 0 1 .4 1 1 0 1.3.2 2.5.6 3.6.1.3 0 .7-.2 1z"/></svg>
          703-555-0142
        </div>
        <div class="contact__line">
          <svg viewBox="0 0 24 24" aria-hidden="true"><path fill="var(--sky)" d="M2 5h20v14H2z"/><path fill="none" stroke="#fff" stroke-width="2" d="M2 5l10 8 10-8"/></svg>
          prattdq47@mailvessa.com
        </div>
      </div>

      <svg class="card__band" viewBox="0 0 560 26" preserveAspectRatio="none" aria-hidden="true">
        <polygon points="0,14 380,14 372,26 0,26" fill="var(--navy)"/>
        <polygon points="386,6 560,6 560,26 378,26" fill="var(--sky)"/>
      </svg>
    </section>
  </main>
</body>
</html>
```